Business Card Design

Company is a Commercial Building Company specialising in New Construction and existing refurbishments

Industry/Entity Type

Business

Contact Information for Business Card

Liam Porter
Construction Manager
E Liam@marshbuilding.com.au
M 0400 213 594
Mail 14 Tarrant Rise Harbourvale WA 6390

```html
<!DOCTYPE html>
<html lang="en">
<head>
<meta charset="utf-8">
<title>Marsh Building &amp; Construction – Business Card</title>
<link href="https://fonts.googleapis.com/css2?family=Arimo:wght@400;700&display=swap" rel="stylesheet">
<style>
  :root {
    --stage: #3a3b3e;
    --card-dark: #000000;
    --card-light: #f7f9fa;
    --ink-light: #ffffff;
    --ink-dark: #1c1f3a;
    --ink-body: #111111;
    --accent-cyan: #1db7df;
    --accent-orange: #ee8a1c;
  }
  * { box-sizing: border-box; margin: 0; padding: 0; }
  html, body {
    width: 1200px; height: 960px; overflow: hidden;
    background: var(--stage);
    font-family: "Arimo", Arial, sans-serif;
  }
  .sheet {
    width: 1200px; height: 960px;
    display: flex; flex-direction: column;
    align-items: center; justify-content: center; gap: 40px;
  }
  .card {
    width: 760px; height: 434px;
    border-radius: 34px;
    position: relative;
    box-shadow: 0 10px 30px rgba(0,0,0,.35);
  }
  .card--front { background: var(--card-dark); }
  .card--back { background: var(--card-light); }

  .brand {
    position: absolute;
    display: flex; align-items: center; gap: 14px;
    font-weight: 700; text-transform: uppercase;
    letter-spacing: 1px; line-height: 1.15;
  }
  .brand__mark { width: 22px; height: 22px; flex: none; }
  .card--front .brand {
    left: 50%; top: 50%; transform: translate(-50%, -50%);
    color: var(--ink-light); font-size: 30px;
  }
  .card--front .brand__mark { background: var(--accent-cyan); }
  .card--back .brand {
    left: 200px; top: 70px;
    color: var(--ink-dark); font-size: 24px;
  }
  .card--back .brand__mark { background: var(--accent-orange); width: 18px; height: 18px; }

  .contact {
    position: absolute; left: 440px; top: 185px;
    list-style: none; font-size: 17px; color: var(--ink-body);
    line-height: 1.3;
  }
  .contact li { display: flex; align-items: flex-start; gap: 12px; }
  .contact svg { width: 15px; height: 15px; flex: none; margin-top: 2px; fill: var(--ink-body); }

  .person { position: absolute; left: 56px; bottom: 60px; color: var(--ink-body); }
  .person__name { font-size: 36px; font-weight: 400; }
  .person__role { font-size: 19px; margin-top: 2px; }
</style>
</head>
<body>
<main class="sheet">
  <section class="card card--front" aria-label="Card front">
    <div class="brand">
      <span class="brand__mark"></span>
      <span>Marsh Building<br>&amp; Construction</span>
    </div>
  </section>

  <section class="card card--back" aria-label="Card back">
    <div class="brand">
      <span class="brand__mark"></span>
      <span>Marsh Building<br>&amp; Construction</span>
    </div>

    <ul class="contact">
      <li>
        <svg viewBox="0 0 16 16" aria-hidden="true"><rect x="4" y="1" width="8" height="14" rx="1.5"/><rect x="5.5" y="3" width="5" height="8" fill="#f7f9fa"/></svg>
        <span>0400 213 594</span>
      </li>
      <li>
        <svg viewBox="0 0 16 16" aria-hidden="true"><rect x="1" y="3" width="14" height="10" rx="1"/><path d="M1.5 3.5 8 9l6.5-5.5" stroke="#f7f9fa" stroke-width="1.4" fill="none"/></svg>
        <span>Liam@marshbuilding.com.au</span>
      </li>
      <li>
        <svg viewBox="0 0 16 16" aria-hidden="true"><path d="M8 1a5 5 0 0 0-5 5c0 3.8 5 9 5 9s5-5.2 5-9a5 5 0 0 0-5-5zm0 7a2 2 0 1 1 0-4 2 2 0 0 1 0 4z"/></svg>
        <span>14 Tarrant Rise<br>Harbourvale WA 6390</span>
      </li>
    </ul>

    <div class="person">
      <p class="person__name">Liam Porter</p>
      <p class="person__role">Construction Manager</p>
    </div>
  </section>
</main>
</body>
</html>
```